Buch-/eBook-Cover für Traumatherapeutin
Zielgruppe
Ich bin Traumatherapeutin und schreibe ein Buch zum Thema Trauma bearbeiten.
Meine Zielgruppe sucht Heilung, Genesung, Selbstliebe etc.
Aufgabenstellung
Buchcover
Bitte erstell mir ein modernes positives inspirierendes Buchcover mit dem
Titel: 'Morgenlicht NEU entdecken“
Untertitel: „Spüre den Mut der ganz in dir wohnt“
Dr. Mira Kessow
Ich hätte gerne ein modernes Buch, das entweder einen Bezug zum Thema Trauma hat oder aber einfach stylische Schriftzüge. Bin aber auch offen für andere Vorschläge.
Dunkelblau, weiß und türkis oder auch rosa mag ich ganz gerne. Wobei Dunkelblau, weiß und türkis meine Favoriten sind und mit rosa höchstens kleinere Akzente gesetzt werden sollten.
Das Buchcover soll modern sein und direkt ansprechen. Gerne eine originelle Lösung, oder etwas Besonderes, etwas das Tiefe ausdrückt, oder man mehrmals hinsehen muss um etwas zu erkennen oder etwas das mehr Interpretationsspielraum lässt.
Gerne auch viel weiß, zumindest heller und nicht zu dunkel. Stylish, aber nicht überfrachtet.
Schreib mich gerne an, wenn du Fragen hast.
Ich habe mal zwei Beispiel von Typolösungen angehängt, die ich ganz cool fände.
Ich freue mich auf deine Ideen :-)
Ganz liebe Grüße
Mira

```html
<!DOCTYPE html>
<html lang="de">
<head>
<meta charset="utf-8">
<title>Morgenlicht NEU entdecken – Buchcover</title>
<link rel="stylesheet" href="https://fonts.googleapis.com/css2?family=Caveat+Brush&family=Montserrat:wght@400;500&display=swap">
<style>
  :root {
    --bg: #6f6f70;
    --blue-deep: #1a82c9;
    --blue-mid: #2c96d4;
    --blue-light: #8fd0e8;
    --white: #f4f4f0;
    --pink: #ec2a8b;
  }
  html, body {
    margin: 0;
    width: 1200px;
    height: 1200px;
    overflow: hidden;
    background: var(--bg);
  }
  .cover {
    position: absolute;
    left: 210px;
    top: 50px;
    width: 780px;
    height: 1100px;
    background:
      radial-gradient(ellipse 70% 45% at 82% 10%, var(--blue-light) 0%, rgba(143,208,232,0.35) 45%, rgba(143,208,232,0) 80%),
      linear-gradient(180deg, var(--blue-mid) 0%, var(--blue-deep) 100%);
    color: var(--white);
    overflow: hidden;
  }
  .cover__spine-line {
    position: absolute;
    left: 36px;
    top: 0;
    width: 2px;
    height: 100%;
    background: rgba(255,255,255,0.12);
  }
  .title {
    position: absolute;
    left: 40px;
    right: 0;
    top: 0;
    margin: 0;
    font-family: "Caveat Brush", cursive;
    font-weight: 400;
    text-align: center;
  }
  .title__line {
    position: absolute;
    left: 0;
    right: 0;
    display: block;
    line-height: 1;
  }
  .title__top { top: 100px; font-size: 108px; }
  .title__accent { top: 218px; font-size: 214px; letter-spacing: 2px; }
  .title__bottom { top: 452px; font-size: 126px; }
  .underline {
    position: absolute;
    left: 78px;
    top: 418px;
    width: 660px;
    height: 40px;
  }
  .subtitle {
    position: absolute;
    left: 40px;
    right: 0;
    top: 672px;
    margin: 0;
    font-family: "Montserrat", sans-serif;
    font-weight: 500;
    font-size: 30px;
    line-height: 1.2;
    text-align: center;
  }
  .author {
    position: absolute;
    left: 40px;
    right: 0;
    top: 1030px;
    margin: 0;
    font-family: "Montserrat", sans-serif;
    font-weight: 400;
    font-size: 23px;
    text-align: center;
  }
</style>
</head>
<body>
  <main class="cover">
    <div class="cover__spine-line"></div>
    <h1 class="title">
      <span class="title__line title__top">Morgenlicht</span>
      <span class="title__line title__accent">NEU</span>
      <span class="title__line title__bottom">entdecken</span>
    </h1>
    <svg class="underline" viewBox="0 0 660 40" aria-hidden="true">
      <path d="M2 18 C180 12 420 8 620 10 L618 16 C420 16 200 20 10 26 Z" fill="var(--pink)"/>
      <path d="M12 30 C220 24 460 20 656 16 L650 24 C460 28 240 32 14 38 Z" fill="var(--pink)"/>
    </svg>
    <p class="subtitle">Spüre den Mut<br>der ganz in dir wohnt</p>
    <p class="author">Dr. Mira Kessow</p>
  </main>
</body>
</html>
```